Business Card Design - Amberfield Court

We are looking at a new design for our business cards that has a modern and professional look. We run a residential aged care facility focussing on the care of residents. The cards will be used for potential clients, consultants and business opportunities in this sector. Blue and white is our main colours and would to see these colours incorporated in the design.
Industry/Entity Type
Business
Contact Information for Business Card
Amberfield Court, Darren Walsh, dwalsh@amberfieldcourt.com.au, Finance Manager, 0472 639 208, BCom, 37 Marrabel Crescent, Brindle Vale, Qld 4093.
Look and feel
Each slider illustrates characteristics of the customer's brand and the style your logo design should communicate.

```html
<!DOCTYPE html>
<html lang="en">
<head>
<meta charset="utf-8">
<title>Amberfield Court – Business Card</title>
<link rel="stylesheet" href="https://fonts.googleapis.com/css2?family=Open+Sans:wght@400;600&display=swap">
<style>
  :root {
    --page-bg: #ecebe8;
    --brand-blue: #3f6d88;
    --brand-blue-dark: #2f566e;
    --brand-blue-light: #5b8aa5;
    --card-white: #ffffff;
    --text-dark: #2b2b2b;
    --text-grey: #a39c95;
    --tag-taupe: #a89d94;
  }
  * { box-sizing: border-box; margin: 0; padding: 0; }
  html, body { width: 1200px; height: 950px; overflow: hidden; }
  body {
    background: var(--page-bg);
    font-family: "Open Sans", Arial, sans-serif;
    position: relative;
  }
  .card {
    position: absolute;
    left: 220px;
    width: 760px;
    height: 430px;
    border-radius: 4px;
    box-shadow: 0 10px 28px rgba(0,0,0,0.18);
    overflow: hidden;
  }
  /* Back side */
  .card-back {
    top: 40px;
    background: linear-gradient(135deg, var(--brand-blue-light) 0%, var(--brand-blue) 55%, var(--brand-blue-dark) 100%);
    display: flex;
    flex-direction: column;
    align-items: center;
    justify-content: center;
    gap: 14px;
  }
  .brand {
    display: flex;
    align-items: center;
    gap: 14px;
  }
  .brand-dot {
    width: 26px; height: 26px;
    border-radius: 50%;
    flex: none;
  }
  .brand-name {
    font-weight: 600;
    letter-spacing: 0.08em;
    text-transform: uppercase;
    white-space: nowrap;
  }
  .card-back .brand-dot { background: var(--card-white); }
  .card-back .brand-name { color: var(--card-white); font-size: 40px; }
  .card-back .tagline { color: #dce7ee; font-size: 20px; }

  /* Front side */
  .card-front {
    top: 500px;
    background: linear-gradient(160deg, #ffffff 0%, #ffffff 60%, #f1f1f1 100%);
  }
  .card-front .brand-block {
    position: absolute;
    left: 48px; top: 48px;
  }
  .card-front .brand-dot { background: var(--brand-blue); width: 22px; height: 22px; }
  .card-front .brand-name { color: var(--brand-blue); font-size: 28px; }
  .card-front .tagline {
    display: inline-block;
    margin-top: 10px;
    background: var(--tag-taupe);
    color: #fff;
    font-size: 15px;
    padding: 3px 14px;
  }
  .contact-list {
    position: absolute;
    left: 48px; top: 220px;
    list-style: none;
    color: var(--text-dark);
    font-size: 18px;
    line-height: 1.55;
  }
  .contact-list li { display: flex; align-items: center; gap: 10px; white-space: nowrap; }
  .contact-list svg { width: 18px; height: 18px; fill: var(--brand-blue); flex: none; }
  .contact-list .address { margin-top: 2px; }
  .person {
    position: absolute;
    right: 70px; top: 230px;
    text-align: left;
    white-space: nowrap;
  }
  .person-name {
    color: var(--brand-blue);
    font-size: 26px;
    font-weight: 600;
  }
  .person-name .credential { font-size: 19px; }
  .person-role { color: var(--text-grey); font-size: 19px; }
  .edge-tab {
    position: absolute;
    right: 0; top: 238px;
    width: 14px; height: 44px;
    background: var(--brand-blue);
  }
</style>
</head>
<body>
  <section class="card card-back" aria-label="Card back">
    <div class="brand">
      <span class="brand-dot"></span>
      <span class="brand-name">Amberfield Court</span>
    </div>
    <p class="tagline">Comfort, Respect, Community</p>
  </section>

  <section class="card card-front" aria-label="Card front">
    <div class="brand-block">
      <div class="brand">
        <span class="brand-dot"></span>
        <span class="brand-name">Amberfield Court</span>
      </div>
      <p class="tagline">Comfort, Respect, Community</p>
    </div>

    <ul class="contact-list">
      <li>
        <svg viewBox="0 0 24 24" aria-hidden="true"><path d="M6.6 10.8a15.1 15.1 0 0 0 6.6 6.6l2.2-2.2a1 1 0 0 1 1-.25 11.4 11.4 0 0 0 3.6.57 1 1 0 0 1 1 1V20a1 1 0 0 1-1 1A17 17 0 0 1 3 4a1 1 0 0 1 1-1h3.5a1 1 0 0 1 1 1c0 1.25.2 2.45.57 3.6a1 1 0 0 1-.25 1z"/></svg>
        0472 639 208
      </li>
      <li>
        <svg viewBox="0 0 24 24" aria-hidden="true"><path d="M2 5h20v14H2z M2 5l10 8 10-8" fill="none" stroke="#3f6d88" stroke-width="2"/></svg>
        dwalsh@amberfieldcourt.com.au
      </li>
      <li>
        <svg viewBox="0 0 24 24" aria-hidden="true"><circle cx="12" cy="12" r="10"/><path d="M2 12h20M12 2c3 3 3 17 0 20M12 2c-3 3-3 17 0 20" fill="none" stroke="#fff" stroke-width="1.5"/></svg>
        www.amberfieldcourt.com.au
      </li>
      <li class="address">37 Marrabel Crescent, Brindle Vale, Qld 4093.</li>
    </ul>

    <div class="person">
      <p class="person-name">Darren Walsh <span class="credential">BCom</span></p>
      <p class="person-role">Finance Manager</p>
    </div>
    <span class="edge-tab"></span>
  </section>
</body>
</html>
```